Corvane Capital Business Cards

These are professional business cards that are for my family office.
Put fake emails and phone numbers as of now until I finalize those components. This family office controls my families investments, assets, and future. The cards should be professional.
..
.
.
.
I just uploaded another variation of a logo I would like to see as a business card to I am inbeteen which logo to use

Target Market(s)

business

Industry/Entity Type

business

Contact Information for Business Card

Professional, wealth related, finance related.

Requirements
Must have
• Logo

```html
<!DOCTYPE html>
<html lang="en">
<head>
<meta charset="UTF-8">
<title>Corvane Capital Business Cards</title>
<link href="https://fonts.googleapis.com/css2?family=Playfair+Display:wght@400;500&family=Poppins:wght@300;400&display=swap" rel="stylesheet">
<style>
  :root {
    --backdrop: #2b2b2b;
    --card: #0a0a0a;
    --gold: #d9b877;
    --gold-light: #f0d9a4;
    --gold-dark: #b38f4f;
    --ink: #0a0a0a;
  }
  * { margin: 0; padding: 0; box-sizing: border-box; }
  html, body {
    width: 1200px;
    height: 1015px;
    overflow: hidden;
    background: var(--backdrop);
  }
  .stage {
    width: 1200px;
    height: 1015px;
    display: flex;
    flex-direction: column;
    align-items: center;
    justify-content: center;
    gap: 60px;
  }
  .card {
    position: relative;
    width: 620px;
    height: 354px;
    background: var(--card);
    box-shadow: 0 14px 30px rgba(0,0,0,0.45);
    overflow: hidden;
  }
  .card__rule {
    position: absolute;
    left: 0;
    right: 0;
    bottom: 12px;
    height: 3px;
    background: linear-gradient(90deg, var(--gold-dark), var(--gold-light), var(--gold));
  }
  .gold-text {
    color: var(--gold);
  }

  /* Front */
  .card--front {
    display: flex;
    flex-direction: column;
    align-items: center;
    justify-content: center;
    gap: 22px;
  }
  .brand-mark {
    width: 54px;
    height: 54px;
    background: linear-gradient(135deg, var(--gold-light), var(--gold-dark));
  }
  .brand-name {
    font-family: "Playfair Display", serif;
    font-weight: 400;
    font-size: 38px;
    letter-spacing: 4px;
    text-transform: uppercase;
    color: var(--gold);
  }

  /* Back */
  .card--back {
    padding: 58px 0 0 56px;
  }
  .person__name {
    font-family: "Playfair Display", serif;
    font-weight: 400;
    font-size: 24px;
    letter-spacing: 2px;
    text-transform: uppercase;
    color: var(--gold);
    line-height: 1.1;
  }
  .person__role {
    font-family: "Poppins", sans-serif;
    font-weight: 300;
    font-size: 15px;
    color: var(--gold);
    margin-top: 2px;
  }
  .contact-list {
    list-style: none;
    margin-top: 46px;
    display: flex;
    flex-direction: column;
    gap: 6px;
  }
  .contact-list__item {
    display: flex;
    align-items: center;
    gap: 12px;
    font-family: "Poppins", sans-serif;
    font-weight: 300;
    font-size: 15px;
    color: var(--gold);
  }
  .contact-list__icon {
    width: 22px;
    height: 22px;
    flex: none;
  }
  .address {
    margin-top: 36px;
    font-family: "Poppins", sans-serif;
    font-weight: 300;
    font-size: 15px;
    line-height: 1.35;
    color: var(--gold);
    font-style: normal;
  }
  .back-brand {
    position: absolute;
    right: 56px;
    top: 70px;
    display: flex;
    flex-direction: column;
    align-items: center;
    gap: 18px;
  }
  .back-brand__mark {
    width: 150px;
    height: 150px;
    background: linear-gradient(135deg, var(--gold-light), var(--gold-dark));
  }
  .back-brand__name {
    font-family: "Playfair Display", serif;
    font-size: 18px;
    letter-spacing: 3px;
    text-transform: uppercase;
    color: var(--gold);
  }
</style>
</head>
<body>
<main class="stage">

  <section class="card card--front" aria-label="Business card front">
    <div class="brand-mark" aria-hidden="true"></div>
    <h1 class="brand-name">Corvane Capital</h1>
    <div class="card__rule"></div>
  </section>

  <section class="card card--back" aria-label="Business card back">
    <div class="person">
      <h2 class="person__name">Daniel Harrow</h2>
      <p class="person__role">Managing Director</p>
    </div>

    <ul class="contact-list">
      <li class="contact-list__item">
        <svg class="contact-list__icon" viewBox="0 0 22 22" aria-hidden="true">
          <circle cx="11" cy="11" r="11" fill="#d9b877"/>
          <path d="M7.5 6.5 L9.3 6.5 L10 9 L8.9 9.9 Q9.8 12 12.1 13.1 L13 12 L15.5 12.7 L15.5 14.5 Q15.5 15.5 14.4 15.5 Q7.5 15 6.5 7.6 Q6.5 6.5 7.5 6.5 Z" fill="#0a0a0a"/>
        </svg>
        044-987 654 321
      </li>
      <li class="contact-list__item">
        <svg class="contact-list__icon" viewBox="0 0 22 22" aria-hidden="true">
          <circle cx="11" cy="11" r="11" fill="#d9b877"/>
          <rect x="5.5" y="7" width="11" height="8" fill="#0a0a0a"/>
          <path d="M5.5 7 L11 11.5 L16.5 7" fill="none" stroke="#d9b877" stroke-width="1"/>
        </svg>
        info@corvanecap.com
      </li>
      <li class="contact-list__item">
        <svg class="contact-list__icon" viewBox="0 0 22 22" aria-hidden="true">
          <circle cx="11" cy="11" r="11" fill="#d9b877"/>
          <g fill="none" stroke="#0a0a0a" stroke-width="1.1">
            <circle cx="11" cy="11" r="5.5"/>
            <ellipse cx="11" cy="11" rx="2.4" ry="5.5"/>
            <line x1="5.5" y1="11" x2="16.5" y2="11"/>
          </g>
        </svg>
        www.corvanecapital.com
      </li>
    </ul>

    <address class="address">
      318, Harbour Lane, Suite 5<br>
      45120, Ashford
    </address>

    <div class="back-brand">
      <div class="back-brand__mark" aria-hidden="true"></div>
      <span class="back-brand__name">Corvane Capital</span>
    </div>

    <div class="card__rule"></div>
  </section>

</main>
</body>
</html>
```